Business card design for a dynamic IT consulting company

We need a business card design for a young firm, specialized in the Telecommunications/Consulting industry. The name of the company is Quindor and Partners Business Consulting Ltd. (Short name: Quindor and Partnes)
Quindor = solve read reverse, so we aim to be uncomplicated and solution-oriented. The small pipe in our logo is also related to the word solve. So we need a new business card design, which is simple, eye catching and something non traditional (I would probably prefer a square shaped design rather than a rectangle, but open for suggestions). Attached our logo.

Target Market(s)

Usually our customers are Tier1 Telecoms providers (Q-Netra, Palorix, etc) and their executives.

Industry/Entity Type

Business

Contact Information for Business Card

Name: Bence Tolnavari
Email: b.tolnavari@quindor.hu
Web: www.quindor.hu
Mobile: +36 30 518 2769
Title: Managing Director

Optional:
Company name: Quindor and Partners Ltd.
Address: 1087 Budapest, Tolvenka str. 28/C, Hungary

Font styles to use
Other font styles liked:
• helveticaneue_medium, Prime Regular are used now.

Colors

Designer to choose colors to be used in the design.

Requirements
Must have
• I would like to have a 2 sided design.
Nice to have
• I thought if we make the logo a bit bigger (without the company name), that could go to the back with the company name below. I though, if the pipe in the logo is somehow touchable on the business card, would be nice and unique.

```html
<!DOCTYPE html>
<html lang="en">
<head>
<meta charset="utf-8">
<title>Quindor and Partners – Business Card</title>
<link rel="stylesheet" href="https://fonts.googleapis.com/css2?family=Work+Sans:wght@400;500&family=Oswald:wght@600&display=swap">
<style>
  :root {
    --backdrop: #0e0e0e;
    --card: #1f1f1f;
    --card-edge: #262626;
    --foil: #cfcfcf;
    --emboss: #141414;
    --emboss-light: #353535;
    --rule: #6f6f6f;
  }
  * { box-sizing: border-box; margin: 0; padding: 0; }
  html, body { width: 1200px; height: 900px; overflow: hidden; }
  body {
    background: radial-gradient(ellipse at 55% 40%, #1c1c1c 0%, var(--backdrop) 70%);
    font-family: "Work Sans", Arial, sans-serif;
    position: relative;
  }
  .card {
    position: absolute;
    left: 290px;
    width: 620px;
    height: 360px;
    background: linear-gradient(135deg, var(--card-edge) 0%, var(--card) 55%, #1a1a1a 100%);
    box-shadow: 0 18px 40px rgba(0,0,0,0.7);
  }
  .card--front { top: 70px; }
  .card--back  { top: 470px; }

  .company-name {
    position: absolute;
    left: 0; right: 0;
    text-align: center;
    font-weight: 500;
    font-size: 40px;
    line-height: 1;
    color: var(--foil);
  }
  .card--front .company-name { top: 150px; }
  .card--back  .company-name { top: 52px; }

  .front-web {
    position: absolute;
    bottom: 36px; left: 0; right: 0;
    text-align: center;
    font-size: 15px;
    letter-spacing: 3px;
    color: var(--emboss);
    text-shadow: 0 1px 0 var(--emboss-light);
  }

  .person {
    position: absolute;
    top: 160px; right: 350px;
    text-align: right;
  }
  .person__name {
    font-family: "Oswald", "Arial Narrow", sans-serif;
    font-weight: 600;
    font-size: 30px;
    letter-spacing: 0.5px;
    color: var(--emboss);
    text-shadow: 0 1px 0 var(--emboss-light);
    line-height: 1.1;
  }
  .person__title {
    font-size: 15px;
    letter-spacing: 1.5px;
    color: var(--emboss);
    text-shadow: 0 1px 0 var(--emboss-light);
  }
  .divider {
    position: absolute;
    top: 158px; left: 290px;
    width: 1px; height: 72px;
    background: var(--rule);
  }
  .contacts {
    position: absolute;
    top: 162px; left: 312px;
    list-style: none;
  }
  .contacts li {
    display: flex;
    align-items: center;
    gap: 12px;
    font-size: 16px;
    line-height: 22px;
    color: var(--foil);
  }
  .contacts svg { width: 13px; height: 13px; flex: none; }
  .address {
    position: absolute;
    top: 272px; left: 0; right: 0;
    text-align: center;
    font-size: 16px;
    line-height: 22px;
    color: var(--emboss);
    text-shadow: 0 1px 0 var(--emboss-light);
  }
  .address__company { font-weight: 500; letter-spacing: 1px; }
</style>
</head>
<body>

<section class="card card--front">
  <div class="company-name">Quindor and Partners</div>
  <div class="front-web">www.quindor.hu</div>
</section>

<section class="card card--back">
  <div class="company-name">Quindor and Partners</div>

  <div class="person">
    <div class="person__name">BENCE TOLNAVARI</div>
    <div class="person__title">MANAGING DIRECTOR</div>
  </div>

  <div class="divider"></div>

  <ul class="contacts">
    <li>
      <svg viewBox="0 0 16 16" aria-hidden="true"><path fill="#cfcfcf" d="M3.6 1.2l2.3 2.6-1.3 1.7c.9 2 2.3 3.4 4.3 4.3l1.7-1.3 2.6 2.3-1.2 2.5C7 13.2 2.8 9 1.2 3.6z"/></svg>
      +36 30 518 2769
    </li>
    <li>
      <svg viewBox="0 0 16 16" aria-hidden="true"><rect x="1" y="3" width="14" height="10" fill="#cfcfcf"/><path d="M1 3l7 6 7-6" fill="none" stroke="#1f1f1f" stroke-width="1.4"/></svg>
      b.tolnavari@quindor.hu
    </li>
    <li>
      <svg viewBox="0 0 16 16" aria-hidden="true"><g fill="none" stroke="#cfcfcf" stroke-width="1.4"><circle cx="8" cy="8" r="6.5"/><ellipse cx="8" cy="8" rx="3" ry="6.5"/><path d="M1.5 8h13"/></g></svg>
      www.quindor.hu
    </li>
  </ul>

  <div class="address">
    <div class="address__company">QUINDOR AND PARTNERS LTD:</div>
    <div>1087 Budapest, Tolvenka str. 28/C, Hungary</div>
  </div>
</section>

</body>
</html>
```